Letterhead Design for Law Firm

**Edit: I have added the photo of a bottom that I like.

------
We are looking for a re-design of our new letterhead. The letterhead is for a law firm and will be used for digital and traditionally printed correspondence.

Here are some suggestions:

- Please use colours are #8ec900 and simple black.
- Please do not use any type of "waves" at the bottom of the page. This is not in style at all.
- Please stay modern yet conservative.
- Please use font Segoe UI Light or similar if you can
- Avoid clipart or illustrations.
- Utilize ample white space in the layout so the design looks clean and information is easy to read at a glance. Don't overcrowd the letterhead.
- Make sure the letterhead design is consistent with our brand identity (see corvelith.ca)
-Please, no black headers or footers.

I am attaching my current letterhead and signature for your convenience.

Remember, the letterhead is an extension of our professional identity. We are a successful firm and trial lawyers who correspond with insurers, judges, lawyers, courts, clients, etc. Make it new, modern, attractive, yet powerful and conservative.

It needs to be easily printable. I would like the bleed removed in print so the black bar the bottom crosses the page (but the text is not near the edges)
Updates

Low design quality

Target Market(s)

Clients, Government Offices, Judiciary, Lawyers, Insurance Companies, Colleagues.

Industry/Entity Type

Law

Other font styles liked:
• Segoe UI LIght, Calibri Light,

Colors
00AB8E
00BBA5
67D7C9
C6EFE9
E9F9F6

Requirements
Must have
• Everything that is on the letterhead now.
Nice to have
• Cutting Edge design, yet conservative.
Should not have
• law firm cliche design, images,

```html
<!DOCTYPE html>
<html lang="en">
<head>
<meta charset="utf-8">
<title>Corvelith Letterhead</title>
<link rel="stylesheet" href="https://fonts.googleapis.com/css2?family=Open+Sans:wght@300;400;600&display=swap">
<style>
  :root {
    --brand-green: #8ec900;
    --brand-black: #0b0b0b;
    --fold-grey: #4a4a4a;
    --ink: #1a1a1a;
    --paper: #ffffff;
    --backdrop: #d9d9d9;
    --sig-tone: #ececec;
  }
  * { box-sizing: border-box; margin: 0; padding: 0; }
  html, body {
    width: 1200px; height: 1155px; overflow: hidden;
    background: var(--backdrop);
    font-family: "Open Sans", sans-serif;
    color: var(--ink);
  }
  .letterhead {
    position: absolute; left: 170px; top: 21px;
    width: 860px; height: 1113px;
    background: var(--paper);
    box-shadow: 0 4px 18px rgba(0,0,0,.18);
    overflow: hidden;
  }
  .bands { position: absolute; inset: 0; }
  .firm-name {
    position: absolute; left: 72px; top: 34px;
    font-weight: 300; font-size: 58px; letter-spacing: 3px;
    color: var(--paper); line-height: 1;
  }
  .contact-block {
    position: absolute; left: 650px; top: 96px;
    padding-left: 12px; border-left: 2px solid var(--brand-green);
    font-size: 11px; line-height: 14.5px; font-weight: 400;
    font-style: normal;
  }
  .contact-block b { font-weight: 600; }
  .contact-block .web-accent { color: var(--brand-green); font-weight: 600; }
  .contact-block .practice { margin-top: 10px; }
  .letter-body { position: absolute; left: 110px; top: 215px; font-size: 13.5px; line-height: 19px; font-weight: 300; }
  .strong { font-weight: 600; }
  .date { margin-top: 14px; margin-left: 14px; }
  .delivery { margin-top: 14px; margin-left: 28px; }
  .recipient { margin-top: 12px; margin-left: 42px; }
  .attention { margin-top: 18px; margin-left: 56px; }
  .salutation { margin-top: 18px; margin-left: 66px; }
  .subject {
    position: relative; margin-top: 18px; margin-left: 80px;
    width: 610px; padding-bottom: 14px; border-bottom: 1px solid var(--ink);
    display: flex;
  }
  .subject .label { width: 200px; font-weight: 600; padding-top: 38px; }
  .subject .lines { font-weight: 600; }
  .closing { position: absolute; left: 360px; top: 780px; font-size: 13.5px; line-height: 19px; font-weight: 300; }
  .closing .firm { font-weight: 600; text-transform: uppercase; }
  .signature-area {
    width: 190px; height: 62px; margin: 6px 0 4px 20px;
    background: linear-gradient(90deg, var(--sig-tone), #f7f7f7);
  }
  .closing .signer { margin-left: 20px; }
  .closing .corp { margin-left: 20px; font-weight: 600; font-size: 12.5px; }
  .closing .refs { margin-left: 26px; margin-top: 4px; }
</style>
</head>
<body>
  <div class="letterhead">
    <svg class="bands" viewBox="0 0 860 1113" width="860" height="1113">
      <polygon points="0,0 645,0 632,135 0,135" fill="var(--brand-green)"/>
      <polygon points="645,0 860,0 860,70 636,70 600,92" fill="var(--brand-black)"/>
      <polygon points="600,92 636,70 624,112" fill="var(--fold-grey)"/>
      <polygon points="0,1045 700,1045 682,1113 0,1113" fill="var(--brand-green)"/>
      <polygon points="716,1028 860,1028 860,1090 700,1090" fill="var(--brand-black)"/>
    </svg>

    <div class="firm-name">CORVELITH</div>

    <address class="contact-block">
      www.<span class="web-accent">CORVELITH</span>.ca<br>
      48 Harbour Street E., Suite 1210<br>
      Brantwell, ON&nbsp; L9K 2B7<br>
      <b>T:</b> 555-214-3390<br>
      <b>F:</b> 555-214-3391<br>
      <b>File Clerk:</b> Nora Whitfield<br>
      <b>Email:</b> nora@corvelith.ca
      <div class="practice">
        <b>Practice Restricted</b><br>
        Serious Personal Injury<br>
        Wrongful Death Litigation<br>
        Long-Term Disability Litigation<br>
        Wrongful Dismissal Litigation<br>
        Employee Terminations
      </div>
    </address>

    <div class="letter-body">
      <div class="strong">Without Prejudice</div>
      <div class="date">March 13, 2024</div>
      <div class="delivery strong">By Email</div>
      <div class="recipient">
        Northvale Insurance Company<br>
        Claims Litigation Department<br>
        240 Elmridge Road North<br>
        P.O. Box 3100<br>
        Kelsford, ON&nbsp;&nbsp; N3R 5T2
      </div>
      <div class="attention">Attention:&nbsp; Mr. Calden Price</div>
      <div class="salutation">Mr. Price:</div>
      <div class="subject">
        <div class="label">Re:</div>
        <div class="lines">
          Harrow v. Delacour et al.<br>
          DOL:&nbsp; September 12, 2019<br>
          Pre-Mediation Settlement Proposal – March 13<sup>th</sup>, 2024
        </div>
      </div>
    </div>

    <div class="closing">
      <div>Yours very truly,</div>
      <div class="firm">Corvelith Personal Injury Lawyers</div>
      <div class="signature-area" role="img" aria-label="Handwritten signature of Daniel R. Corvelith"></div>
      <div class="signer">Daniel R. Corvelith</div>
      <div class="corp">Corvelith Law Professional Corporation</div>
      <div class="refs">/nw<br>Encl.</div>
    </div>
  </div>
</body>
</html>
```